Vorn upkeep KT Solar Venture

Solar power system install
Services and maintenance
wiring, Rewinding and Renovation
Switch Board Upgrade
Power and lighting point
t doesn’t matter how much you spend on quality parts, your solar system will let you down if your design and installation are sub-par. Have your solar system tailored and installed by our Master Electrician and Bright Grid Guild Accredited team.

Target Market(s)

sales and installed

Industry/Entity Type

Solar install and retailer

Contact Information for Business Card

Name , Email, Phone Number ,Business address,

Font styles to use
Serif

Colors
0054AA
0677BA
7BADD7
CADEEF
E8F1F8

Requirements
Must have
• clear and bright
Nice to have
• new design
Should not have
• unclear pictures

```html
<!DOCTYPE html>
<html lang="en">
<head>
<meta charset="utf-8">
<title>Vorn Upkeep – Business Card</title>
<link rel="stylesheet" href="https://fonts.googleapis.com/css2?family=Roboto:wght@400;500;700;900&display=swap">
<style>
  :root {
    --page-bg: #f2f4f6;
    --blue-deep: #0054aa;
    --blue-mid: #0677ba;
    --blue-soft: #7badd7;
    --blue-pale: #cadeef;
    --blue-mist: #e8f1f8;
    --green: #1f9a3c;
    --ink: #1d1f22;
    --card-white: #f4f4f3;
    --panel-dark: #3a4150;
    --panel-warm: #b89680;
  }
  * { margin: 0; padding: 0; box-sizing: border-box; }
  html, body { width: 1200px; height: 1138px; overflow: hidden; }
  body {
    background: var(--page-bg);
    font-family: "Roboto", Arial, sans-serif;
    position: relative;
  }
  .card {
    position: absolute;
    border-radius: 16px;
    overflow: hidden;
    box-shadow: 0 4px 14px rgba(0,0,0,0.18);
  }
  .card-front { left: 274px; top: 186px; width: 622px; height: 374px; }
  .card-back { left: 276px; top: 608px; width: 618px; height: 374px; background: var(--card-white); }

  .front-art { position: absolute; inset: 0; }

  .front-brand {
    position: absolute;
    right: 30px;
    top: 84px;
    display: flex;
    align-items: center;
    gap: 12px;
    color: #ffffff;
    font-weight: 700;
    font-size: 24px;
    line-height: 1.05;
    text-align: left;
    text-transform: uppercase;
    letter-spacing: 0.5px;
  }
  .brand-dot {
    width: 18px; height: 18px; border-radius: 50%;
    background: var(--blue-mist);
    flex: none;
  }

  .service-list {
    position: absolute;
    right: 28px;
    top: 229px;
    list-style: none;
    text-align: right;
    color: #ffffff;
    font-size: 16px;
    line-height: 22.4px;
  }
  .service-list li::after { content: "  «"; white-space: pre; }

  .back-brand {
    position: absolute;
    left: 32px;
    top: 30px;
    color: var(--blue-deep);
    font-weight: 700;
    font-size: 27px;
    line-height: 1.08;
    text-transform: uppercase;
    letter-spacing: 0.3px;
  }
  .person-name {
    position: absolute;
    left: 32px; top: 134px;
    color: var(--blue-deep);
    font-weight: 500;
    font-size: 26px;
  }
  .person-title {
    position: absolute;
    left: 32px; top: 170px;
    color: var(--ink);
    font-size: 16px;
  }
  .address {
    position: absolute;
    left: 32px; top: 222px;
    color: var(--ink);
    font-size: 16px;
    line-height: 24px;
    font-style: normal;
  }
  .contact-list {
    position: absolute;
    left: 32px; top: 280px;
    list-style: none;
    color: var(--ink);
    font-size: 16px;
    line-height: 23.5px;
  }
  .contact-list li { display: flex; align-items: center; gap: 18px; }
  .contact-list svg { width: 14px; height: 14px; fill: var(--green); flex: none; }
  .back-emblem { position: absolute; left: 380px; top: 110px; }
</style>
</head>
<body>

<section class="card card-front" aria-label="Card front">
  <svg class="front-art" width="622" height="374" viewBox="0 0 622 374">
    <defs>
      <linearGradient id="frontBlue" x1="0" y1="0" x2="0" y2="1">
        <stop offset="0" stop-color="var(--blue-deep)"/>
        <stop offset="1" stop-color="var(--blue-mid)"/>
      </linearGradient>
      <linearGradient id="panelTone" x1="1" y1="0" x2="0" y2="1">
        <stop offset="0" stop-color="var(--panel-warm)"/>
        <stop offset="0.45" stop-color="#5a5f6e"/>
        <stop offset="1" stop-color="var(--panel-dark)"/>
      </linearGradient>
    </defs>
    <rect width="622" height="374" fill="url(#frontBlue)"/>
    <path d="M0 0 H212 Q300 190 206 374 H0 Z" fill="var(--green)"/>
    <path role="img" aria-label="Photo of solar panels catching sunlight"
          d="M0 0 H204 Q288 190 198 374 H0 Z" fill="url(#panelTone)"/>
  </svg>

  <div class="front-brand">
    <span class="brand-dot"></span>
    <span>Vorn Upkeep<br>KT Solar Venture</span>
  </div>

  <ul class="service-list">
    <li>Solar Power System Install</li>
    <li>Services &amp; Maintenance</li>
    <li>Switch Board Upgrade</li>
    <li>Power &amp; Lighting Point</li>
    <li>Wiring, Rewinding &amp; Renovation</li>
  </ul>
</section>

<section class="card card-back" aria-label="Card back">
  <div class="back-brand">Vorn Upkeep<br>KT Solar Venture</div>

  <h1 class="person-name">Aled Marsh</h1>
  <p class="person-title">Managing Director</p>

  <address class="address">17 Harrow Lane, Westvale,<br>Brookfield, US 204518</address>

  <ul class="contact-list">
    <li>
      <svg viewBox="0 0 16 16" aria-hidden="true"><path d="M3 2h3l1.5 3.5-2 1.3a9 9 0 0 0 3.7 3.7l1.3-2L14 10v3a1 1 0 0 1-1 1A11 11 0 0 1 2 3a1 1 0 0 1 1-1z"/></svg>
      <span>555-014-2290</span>
    </li>
    <li>
      <svg viewBox="0 0 16 16" aria-hidden="true"><path d="M1 3h14v10H1z M2 4.2V12h12V4.2L8 8.6z M2.6 4 8 7.6 13.4 4z" fill-rule="evenodd"/></svg>
      <span>aled@vornupkeep.com</span>
    </li>
    <li>
      <svg viewBox="0 0 16 16" aria-hidden="true"><circle cx="8" cy="8" r="7"/><path d="M1.5 8h13M8 1c-2.5 3-2.5 11 0 14M8 1c2.5 3 2.5 11 0 14" stroke="#fff" stroke-width="1" fill="none"/></svg>
      <span>www.vornupkeep.com</span>
    </li>
  </ul>

  <svg class="back-emblem" width="220" height="220" viewBox="0 0 220 220" aria-hidden="true">
    <circle cx="110" cy="110" r="100" fill="var(--blue-pale)"/>
  </svg>
</section>

</body>
</html>
```